redesign of my existing custom website into Wordpress based website

I need someone to redesign my current website into something more classy, simplistic, modern and on trend. I would like it set up on Wordpress in a way thats easy for me to make my own additions to blogs/price changes and promotion banners. I will also need a page that is password protected so members can login and have access to all my training videos and resources.
website is www.tidewellmamas.com.au

Target Market(s)

new mums

Industry/Entity Type

Fitness

Coding

Coded - Design and coding required

Number of Pages Required

5+ page

Colors
33a6d7

Requirements
Must have
• chic, modern, stylish and simplistic.
• a call to action above the page fold
• mobile friendly conversion
• a pop up message as soon as someone enters my sight offering my free report
• a members page that is password protected containing 3 youtube videos and 6 pdf attachments as resources
• a home page
• a contact us page
• an about us page
• a blog page
• a store page
Nice to have
• some examples of my peers websites that I like:
• www.norapellwick.com
• https://www.9qlr.com
• https://41bytedgarth.com
Should not have
• anything gimmicky

```html
<!DOCTYPE html>
<html lang="en">
<head>
<meta charset="utf-8">
<title>Tidewell Mamas — Home</title>
<link href="https://fonts.googleapis.com/css2?family=Nunito+Sans:wght@400;600;700;800&display=swap" rel="stylesheet">
<style>
:root{
  --brand:#33a6d7;
  --brand-deep:#1b6f98;
  --ink:#2a2a2a;
  --muted:#7a7a7a;
  --light:#f4f4f4;
  --white:#ffffff;
  --berry:#b0245a;
  --shade:rgba(0,0,0,.74);
}
*{box-sizing:border-box;margin:0;padding:0}
html,body{width:1200px;height:3614px;overflow:hidden}
body{position:relative;background:var(--white);font-family:"Nunito Sans",Arial,sans-serif;color:var(--ink)}
.section{position:absolute;left:0;width:1200px}
.photo{position:absolute}
.tick-list{list-style:none}
.tick-list li{display:flex;align-items:center;gap:12px;font-size:15px;color:var(--muted);margin-bottom:14px}
.tick{width:18px;height:18px;flex:none}
.btn{display:inline-block;background:var(--brand);color:var(--white);font-weight:700;font-size:15px;letter-spacing:1px;text-transform:uppercase;padding:12px 30px}
.btn-outline{display:inline-block;border:2px solid var(--brand);color:var(--brand);font-weight:700;font-size:14px;padding:9px 22px;text-transform:uppercase}

/* header */
.site-header{top:0;height:101px;background:var(--white);display:flex;align-items:center;padding:0 150px}
.brand{display:flex;align-items:center;gap:12px;font-size:24px;font-weight:700;color:var(--berry)}
.brand-dot{width:44px;height:44px;border-radius:50%;background:var(--berry)}
.main-nav{display:flex;gap:42px;margin-left:auto;font-size:16px;font-weight:600;color:var(--ink)}
.main-nav .current{color:var(--ink);border-bottom:3px solid var(--ink);padding-bottom:34px;margin-bottom:-37px}
.cart{width:42px;height:42px;border-radius:50%;background:var(--berry);margin-left:40px;display:flex;align-items:center;justify-content:center}

/* hero */
.hero{top:101px;height:557px}
.hero .photo{inset:0;background:linear-gradient(120deg,#3d3a40,#6d5a63 45%,#8f3d58 75%,#473f46)}
.hero-copy{position:absolute;left:0;right:0;top:300px;text-align:center;color:var(--white)}
.hero-copy h1{font-size:50px;font-weight:800;line-height:1.1;text-transform:uppercase}
.hero-copy .btn{margin-top:28px}

/* about */
.about{top:658px;height:450px;background:var(--white)}
.about h2{position:absolute;left:150px;top:96px;font-size:34px;font-weight:400}
.about .intro{position:absolute;left:150px;top:150px;width:510px;font-size:14px;line-height:1.6;color:var(--muted)}
.about .tick-list{position:absolute;left:150px;top:218px}
.tips-form{position:absolute;left:723px;top:82px;width:313px;height:299px;background:var(--brand);padding:30px 27px;text-align:center;color:var(--white)}
.tips-form .kicker{font-size:17px;font-weight:700;text-transform:uppercase}
.tips-form .headline{font-size:22px;font-weight:700;margin-top:4px}
.tips-form .field{height:38px;background:var(--white);margin-top:16px}
.tips-form .submit{height:48px;background:#1e1e1e;margin-top:18px;font-size:17px;line-height:48px}
.ball{position:absolute;left:870px;top:-8px;width:76px;height:76px;border-radius:50%;background:radial-gradient(circle at 35% 35%,#e0546a,#b02a3f)}

/* program */
.program{top:1108px;height:458px;background:var(--light)}
.program .photo{left:0;top:0;width:650px;height:458px;background:linear-gradient(100deg,#d9d1c4,#efe9e0 60%,#e7e2da)}
.program h2{position:absolute;left:655px;top:82px;width:420px;font-size:30px;font-weight:400;line-height:1.2}
.program .tick-list{position:absolute;left:655px;top:178px}
.program .btn-outline{position:absolute;left:655px;top:320px}

/* included */
.included{top:1566px;height:487px}
.included .photo{inset:0;background:linear-gradient(110deg,#3a3034,#6a4b55 40%,#8f5664 65%,#3c3437)}
.included-copy{position:absolute;left:0;right:0;top:110px;text-align:center;color:var(--white)}
.included-copy h2{font-size:38px;font-weight:700}
.included-copy p{width:790px;margin:18px auto 0;font-size:17px;line-height:1.6}
.included-copy .btn{margin-top:26px}

/* results */
.results{top:2053px;height:477px;background:linear-gradient(180deg,var(--brand),#2b93c4)}
.results h2{position:absolute;left:0;right:0;top:40px;text-align:center;font-size:32px;font-weight:600;color:var(--white)}
.result-card{position:absolute;top:109px;width:284px;height:323px;background:var(--white);text-align:center}
.result-card .photo{left:0;top:0;width:284px;height:210px;background:linear-gradient(180deg,#eceae6,#d8d3cc)}
.result-card .loss{position:absolute;left:112px;top:178px;width:60px;height:60px;border-radius:50%;background:var(--brand);color:var(--white);font-size:22px;font-weight:800;line-height:60px}
.result-card .loss small{font-size:11px}
.result-card h3{position:absolute;left:0;right:0;top:236px;font-size:28px;font-weight:400;color:var(--brand)}
.result-card p{position:absolute;left:20px;right:20px;top:276px;font-size:12px;line-height:1.5;color:var(--muted)}

/* different */
.different{top:2530px;height:434px;background:var(--white)}
.different h2{position:absolute;left:0;right:0;top:40px;text-align:center;font-size:32px;font-weight:400;color:var(--brand-deep)}
.feature{position:absolute;top:121px;width:284px;height:236px;display:flex;flex-direction:column;align-items:center;justify-content:center;color:var(--white);font-size:18px;font-weight:600;text-align:center;text-transform:uppercase;line-height:1.4}
.feature .photo{inset:0;z-index:0}
.feature span,.feature svg{position:relative;z-index:1}
.feature svg{margin-top:8px}

/* news */
.news{top:2964px;height:313px;background:var(--white)}
.news h2{position:absolute;left:150px;top:20px;font-size:32px;font-weight:400;color:var(--brand)}
.news-arrows{position:absolute;left:958px;top:28px;display:flex;gap:8px}
.news-arrows i{width:24px;height:24px;border-radius:50%;background:#dcdcdc;display:block}
.post{position:absolute;top:90px;width:250px}
.post h3{font-size:18px;font-weight:700;color:var(--berry);line-height:1.3}
.post p{margin-top:16px;font-size:13px;line-height:1.6;color:var(--muted)}

/* footer */
.site-footer{top:3277px;height:337px;background:#2b2b2b;color:#cfcfcf}
.foot-col{position:absolute;top:43px}
.foot-col h4{font-size:16px;font-weight:700;text-transform:uppercase;color:var(--white);margin-bottom:14px}
.foot-col li{list-style:none;font-size:14px;margin-bottom:12px}
.socials{display:flex;gap:10px}
.socials i{display:block;width:28px;height:28px;border-radius:50%;border:2px solid #cfcfcf}
.foot-brand{display:flex;align-items:center;gap:12px;margin-top:36px;font-size:22px;font-weight:700;color:var(--berry)}
.foot-brand b{width:44px;height:44px;border-radius:50%;background:var(--berry);display:block}
.copyright{position:absolute;left:0;right:0;top:290px;text-align:center;font-size:13px}

/* popup */
.shade{position:absolute;inset:0;background:var(--shade)}
.report-popup{position:absolute;left:354px;top:236px;width:482px;height:229px;background:var(--brand);padding:14px}
.report-popup .frame{height:100%;border:2px solid var(--white);text-align:center;color:var(--white);padding-top:26px}
.report-popup h2{font-size:30px;font-weight:800;line-height:1}
.report-popup .sub{font-size:17px;font-weight:700;margin-top:8px}
.report-popup .body{font-size:13px;line-height:1.5;margin:10px auto 0;width:360px}
.report-popup .cta{display:inline-block;margin-top:14px;border:2px solid var(--white);padding:7px 24px;font-size:13px;font-weight:700;text-transform:uppercase}
</style>
</head>
<body>

<header class="section site-header">
  <div class="brand"><span class="brand-dot"></span>Tidewell Mamas</div>
  <nav class="main-nav">
    <span class="current">Home</span><span>About Us</span><span>Program</span><span>Store</span><span>Blog</span><span>Contact Us</span>
  </nav>
  <div class="cart"><svg width="20" height="20" viewBox="0 0 20 20"><path d="M2 3h3l2 10h9l2-7H6" fill="none" stroke="#fff" stroke-width="2"/><circle cx="8" cy="17" r="1.6" fill="#fff"/><circle cx="15" cy="17" r="1.6" fill="#fff"/></svg></div>
</header>

<section class="section hero">
  <div class="photo" role="img" aria-label="Mum exercising at home with her baby in a lounge room"></div>
  <div class="hero-copy">
    <h1>It's time to get fit and<br>spring back into shape</h1>
    <span class="btn">Join the program</span>
  </div>
</section>

<section class="section about">
  <div class="ball" role="img" aria-label="Red exercise ball"></div>
  <h2>About Tidewell Mamas</h2>
  <p class="intro">Short home workouts made for busy new mums, built to fit around naps and feeds so you can regain strength at your own pace.</p>
  <ul class="tick-list">
    <li><svg class="tick" viewBox="0 0 18 18"><circle cx="9" cy="9" r="9" fill="#33a6d7"/><path d="M5 9l3 3 5-6" fill="none" stroke="#fff" stroke-width="2"/></svg>Workouts you can do with baby close by at home</li>
    <li><svg class="tick" viewBox="0 0 18 18"><circle cx="9" cy="9" r="9" fill="#33a6d7"/><path d="M5 9l3 3 5-6" fill="none" stroke="#fff" stroke-width="2"/></svg>Real results from mums in just twelve weeks or less</li>
    <li><svg class="tick" viewBox="0 0 18 18"><circle cx="9" cy="9" r="9" fill="#33a6d7"/><path d="M5 9l3 3 5-6" fill="none" stroke="#fff" stroke-width="2"/></svg>Simple family meals</li>
    <li><svg class="tick" viewBox="0 0 18 18"><circle cx="9" cy="9" r="9" fill="#33a6d7"/><path d="M5 9l3 3 5-6" fill="none" stroke="#fff" stroke-width="2"/></svg>A supportive online mums community</li>
  </ul>
  <div class="tips-form">
    <div class="kicker">Get your free top 10</div>
    <div class="headline">Baby Belly Blasting Tips</div>
    <div class="field"></div>
    <div class="field"></div>
    <div class="submit">Get it Free Now!</div>
  </div>
</section>

<section class="section program">
  <div class="photo" role="img" aria-label="Smiling mum kneeling with dumbbells beside her toddler"></div>
  <h2>12 week Home Workout Program - Basic Pack</h2>
  <ul class="tick-list">
    <li><svg class="tick" viewBox="0 0 18 18"><circle cx="9" cy="9" r="9" fill="#33a6d7"/><path d="M5 9l3 3 5-6" fill="none" stroke="#fff" stroke-width="2"/></svg>Five days a week training plan</li>
    <li><svg class="tick" viewBox="0 0 18 18"><circle cx="9" cy="9" r="9" fill="#33a6d7"/><path d="M5 9l3 3 5-6" fill="none" stroke="#fff" stroke-width="2"/></svg>Full video library with step by step guidance</li>
    <li><svg class="tick" viewBox="0 0 18 18"><circle cx="9" cy="9" r="9" fill="#33a6d7"/><path d="M5 9l3 3 5-6" fill="none" stroke="#fff" stroke-width="2"/></svg>Weekly progress tracking sheets</li>
    <li><svg class="tick" viewBox="0 0 18 18"><circle cx="9" cy="9" r="9" fill="#33a6d7"/><path d="M5 9l3 3 5-6" fill="none" stroke="#fff" stroke-width="2"/></svg>Healthy weekly meal ideas</li>
  </ul>
  <span class="btn-outline">Learn more</span>
</section>

<section class="section included">
  <div class="photo" role="img" aria-label="Mum doing floor exercises on a rug in a living room"></div>
  <div class="included-copy">
    <h2>What's included in the Program?</h2>
    <p>Praesent elementum elit at tellus nec ultrices, sed porttitor mattis enim tempus libero interdum nec interdum vel blandit sed nulla in ullamcorper est eget tempor.</p>
    <span class="btn">Learn more</span>
  </div>
</section>

<section class="section results">
  <h2>Check Our Some Awesome Results</h2>
  <article class="result-card" style="left:157px">
    <div class="photo" role="img" aria-label="Before and after photos of Marisol"></div>
    <div class="loss">12<small>kg</small></div>
    <h3>Marisol</h3>
    <p>Lost twelve kilos in three months and feels stronger than ever.</p>
  </article>
  <article class="result-card" style="left:458px">
    <div class="photo" role="img" aria-label="Before and after photos of TK"></div>
    <div class="loss">10<small>kg</small></div>
    <h3>TK</h3>
    <p>Ten kilos down with workouts done while her baby napped.</p>
  </article>
  <article class="result-card" style="left:757px">
    <div class="photo" role="img" aria-label="Before and after photos of Bea"></div>
    <div class="loss">8<small>kg</small></div>
    <h3>Bea</h3>
    <p>Eight kilos lighter and loving her new energy every day.</p>
  </article>
</section>

<section class="section different">
  <h2>Why Our Program is Different</h2>
  <div class="feature" style="left:152px">
    <div class="photo" role="img" aria-label="Mum working out" style="background:linear-gradient(135deg,#5a4a48,#8c6f66)"></div>
    <span>Specially designed<br>for mums</span>
    <svg width="16" height="16" viewBox="0 0 16 16"><path d="M2 8h11M9 3l5 5-5 5" fill="none" stroke="#fff" stroke-width="2.4"/></svg>
  </div>
  <div class="feature" style="left:460px">
    <div class="photo" role="img" aria-label="Workout equipment" style="background:linear-gradient(135deg,#c9c6c2,#e8e6e3)"></div>
    <span>Workout equipment<br>included</span>
    <svg width="16" height="16" viewBox="0 0 16 16"><path d="M2 8h11M9 3l5 5-5 5" fill="none" stroke="#fff" stroke-width="2.4"/></svg>
  </div>
  <div class="feature" style="left:762px">
    <div class="photo" role="img" aria-label="Fresh healthy food" style="background:linear-gradient(135deg,#2f9ed0,#6cc0e2)"></div>
    <span>Delicious low fat<br>family recipes</span>
    <svg width="16" height="16" viewBox="0 0 16 16"><path d="M2 8h11M9 3l5 5-5 5" fill="none" stroke="#fff" stroke-width="2.4"/></svg>
  </div>
</section>

<section class="section news">
  <h2>Latest News</h2>
  <div class="news-arrows"><i></i><i></i></div>
  <article class="post" style="left:150px">
    <h3>The benefits of moving in the morning</h3>
    <p>An early workout lifts your mood and sets a calm, steady tone for the whole day ahead.</p>
  </article>
  <article class="post" style="left:458px">
    <h3>Marisol's 10 minute lounge room cardio workout</h3>
    <p>No gear needed for this quick circuit you can finish before the next feed comes round.</p>
  </article>
  <article class="post" style="left:793px">
    <h3>Healthy Shepherds Pie Recipe</h3>
    <p>A lighter take on a family classic, packed with vegetables and lean mince everyone loves.</p>
  </article>
</section>

<footer class="section site-footer">
  <div class="foot-col" style="left:150px"><h4>Quick Links</h4><ul><li>Home</li><li>About Us</li><li>Program</li><li>Blog</li></ul></div>
  <div class="foot-col" style="left:361px"><h4>Sublinks</h4><ul><li>Members Area</li><li>Free Report</li><li>Results</li><li>Contact</li></ul></div>
  <div class="foot-col" style="left:562px"><h4>Resources</h4><ul><li>Store</li><li>Recipes</li><li>Videos</li></ul></div>
  <div class="foot-col" style="left:771px">
    <h4>Follow Us</h4>
    <div class="socials"><i></i><i></i><i></i><i></i></div>
    <div class="foot-brand"><b></b>Tidewell Mamas</div>
  </div>
  <p class="copyright">© 2024 Tidewell Mamas. All rights reserved.</p>
</footer>

<div class="shade"></div>

<aside class="report-popup">
  <div class="frame">
    <h2>Get my Free Report Now</h2>
    <p class="sub">Aociosqu litora torquent per conubia</p>
    <p class="body">ostra per inceptos hymenaeos Proin nulla arcu nonummy luctus dictum eget fermentum et lorem Nunc porta</p>
    <span class="cta">Click here</span>
  </div>
</aside>

</body>
</html>
```